Master Template for Print adversiting

Please create a template for print adversiting that we can easily change anytime we will need it for our different campaigns.
We have flight simulors across Europe and Middle East. The simualtors are used mainly by laiks and bought mainly as a gift/experience.
MUST HAVE:
logo, what we do, who we are, website and the main message. OUR font, - see the manual. This message will be changed and based on the seson (Christmas offers, Valentine, Father's Day...etc)
FORMATS:
please create these standard formats: 1/2, 1/4, 1/8, 1/3, 1/6, 1/16
please mix it and create as see the example attached
size is not defined, we will update based on specifif documentation we'll get from magazines
this master will be in German:
Logo: attached - MUST be visible!
What we do/Who we are:
aSKYRO ist der größte Anbieter für Flugsimulatorerlebnisse weltweit und bietet Ihnen 24.000 verschiedene Flughäfen zur Auswahl. Da bleibt kein Wunsch offen!
Website: www.askyro-demo.ch
Main message (should be clear this is the part that will be changed if needed)
Schenken Sie Ihrem Liebsten zu Weihnachten ein Flugticket von aSKYRO und fliegen Sie mit ihm gemeinsam an das Ziel Ihrer Träume.
Attached is the logo manual with pictures. Please combine or use only one of them. Be original. we are looking for a modern design.
Data in jpeg and ai/psp.

```html
<!DOCTYPE html>
<html lang="de">
<head>
<meta charset="utf-8">
<title>aSKYRO – Print-Anzeige Vorlage</title>
<link href="https://fonts.googleapis.com/css2?family=Jost:wght@400;500;600&display=swap" rel="stylesheet">
<style>
  :root {
    --brand-red: #e02127;
    --deep-red: #b3151b;
    --ink: #141414;
    --text-grey: #3a3a3a;
    --paper: #ffffff;
    --stage: #ececec;
    --cockpit-dark: #1c2230;
    --cockpit-mid: #3c4a5e;
    --cockpit-light: #8a96a8;
  }
  * { margin: 0; padding: 0; box-sizing: border-box; }
  html, body {
    width: 1200px;
    height: 902px;
    overflow: hidden;
    background: var(--stage);
    font-family: "Jost", sans-serif;
  }
  .ad {
    position: absolute;
    left: 50px;
    top: 268px;
    width: 1100px;
    height: 366px;
    background: var(--paper);
    overflow: hidden;
  }
  .ad-shapes {
    position: absolute;
    inset: 0;
    width: 100%;
    height: 100%;
  }
  .brand {
    position: absolute;
    left: 26px;
    top: 16px;
    color: var(--paper);
  }
  .brand-url {
    font-size: 18px;
    font-weight: 400;
    line-height: 1;
  }
  .brand-name {
    margin-top: 8px;
    font-size: 42px;
    font-weight: 500;
    line-height: 1;
  }
  .about {
    position: absolute;
    left: 745px;
    top: 26px;
    width: 330px;
    text-align: center;
    font-size: 16px;
    line-height: 1.18;
    color: var(--text-grey);
  }
  .campaign-message {
    position: absolute;
    left: 700px;
    top: 160px;
    width: 380px;
    text-align: center;
    font-size: 20px;
    font-weight: 600;
    line-height: 1.15;
    text-transform: uppercase;
    color: var(--brand-red);
  }
</style>
</head>
<body>
  <section class="ad" aria-label="aSKYRO Anzeige">
    <svg class="ad-shapes" viewBox="0 0 1100 366" xmlns="http://www.w3.org/2000/svg">
      <defs>
        <linearGradient id="cockpitTone" x1="0" y1="0" x2="0" y2="1">
          <stop offset="0" stop-color="#8a96a8"/>
          <stop offset="0.45" stop-color="#3c4a5e"/>
          <stop offset="1" stop-color="#1c2230"/>
        </linearGradient>
      </defs>
      <polygon points="0,0 790,0 750,44 0,44" fill="var(--brand-red)"/>
      <polygon points="0,44 750,44 590,322 0,322" fill="url(#cockpitTone)" role="img" aria-label="Foto: Cockpit eines Flugsimulators mit beleuchteten Instrumenten"/>
      <polygon points="0,0 350,0 300,106 0,106" fill="var(--brand-red)"/>
      <polygon points="0,322 1100,322 1100,366 0,366" fill="var(--brand-red)"/>
      <polygon points="590,322 1100,322 1100,336 582,336" fill="var(--ink)"/>
      <polygon points="610,322 632,322 606,366 584,366" fill="var(--ink)"/>
      <polygon points="645,322 667,322 641,366 619,366" fill="var(--ink)"/>
      <polygon points="980,336 1100,336 1100,366 960,366" fill="var(--deep-red)"/>
      <rect x="1.5" y="1.5" width="1097" height="363" fill="none" stroke="var(--ink)" stroke-width="3"/>
    </svg>

    <div class="brand">
      <p class="brand-url">www.askyro-demo.ch</p>
      <p class="brand-name">aSKYRO</p>
    </div>

    <p class="about">aSKYRO ist der größte Anbieter für Flugsimulatorerlebnisse weltweit und bietet Ihnen 24.000 verschiedene Flughäfen zur Auswahl. Da bleibt kein Wunsch offen!</p>

    <p class="campaign-message">Schenken Sie Ihrem Liebsten zu Weihnachten ein Flugticket von aSKYRO und fliegen Sie mit ihm gemeinsam an das Ziel Ihrer Träume.</p>
  </section>
</body>
</html>
```